Harbourline Electrical Solutions

On one side. LOGO (underneath:) Commercial Industrial Residential

- NAME & CONTACT DETAILS

Marcus T. Hollings
Project Manager

(Cell icon) (441) 555-0187
(Email icon) hlelectricalsolutions@mailvento.com
(Facebook & Instagram icons )@hlelectricalsolutions

Other side: LOGO - underneath ELECTRICAL CONSTRUCTION & MAINTENANCE . LED LIGHTING & AUTOMATION . LIFE SAFETY SYSTEMS (FIRE ALARM / SECURITY) . DATA & COMMUNICATION

```html
<!DOCTYPE html>
<html lang="en">
<head>
<meta charset="utf-8">
<title>Harbourline Electrical Solutions – Business Card</title>
<link rel="stylesheet" href="https://fonts.googleapis.com/css2?family=Lato:wght@400;700&family=Raleway:wght@500;600;700&display=swap">
<style>
  :root {
    --teal: #0f5469;
    --teal-dark: #0b4354;
    --charcoal: #4a4a4a;
    --ink: #3a3a3a;
    --paper: #ffffff;
    --backdrop: #d9d9d9;
  }
  * { box-sizing: border-box; margin: 0; padding: 0; }
  html, body { width: 1200px; height: 802px; overflow: hidden; }
  body {
    background: var(--backdrop);
    position: relative;
    font-family: "Lato", sans-serif;
  }
  .card {
    position: absolute;
    top: 275px;
    width: 442px;
    height: 265px;
    box-shadow: 0 3px 6px rgba(0,0,0,.35);
    overflow: hidden;
  }
  /* Front */
  .card--front { left: 136px; background: var(--paper); }
  .front__stripe {
    position: absolute; left: 0; top: 0; bottom: 0; width: 49px;
    background: var(--teal);
    border-right: 4px solid var(--teal-dark);
  }
  .brand {
    position: absolute;
    display: flex; align-items: center; gap: 10px;
    font-family: "Raleway", sans-serif;
    font-weight: 600;
    text-transform: uppercase;
    letter-spacing: 2px;
  }
  .brand__mark { width: 14px; height: 14px; flex: none; }
  .brand__name { line-height: 1.15; }
  .brand--front { right: 22px; top: 34px; color: var(--teal); font-size: 12.5px; }
  .brand--front .brand__mark { background: var(--teal); }
  .front__sectors {
    position: absolute; right: 20px; top: 92px;
    font-size: 11.6px; color: var(--ink); letter-spacing: .2px;
  }
  .person { position: absolute; left: 71px; top: 127px; }
  .person__name {
    font-family: "Raleway", sans-serif; font-weight: 700;
    font-size: 16px; color: var(--teal);
  }
  .person__role { font-size: 12.5px; color: var(--ink); margin-top: 1px; }
  .contact { position: absolute; left: 71px; top: 178px; font-size: 12.5px; color: var(--ink); }
  .contact__row { display: flex; align-items: center; gap: 4px; height: 16px; }
  .contact__icon { width: 10px; height: 11px; flex: none; }
  .social { position: absolute; left: 71px; top: 231px; font-size: 12.5px; color: var(--ink); display: flex; align-items: center; gap: 6px; }
  .social__dot { width: 14px; height: 14px; border: 1.2px solid var(--teal); border-radius: 50%; flex: none; }

  /* Back */
  .card--back { left: 624px; background: var(--teal); }
  .back__brand-area {
    position: absolute; left: 0; right: 0; top: 0; height: 198px;
    display: flex; align-items: center; justify-content: center;
  }
  .brand--back { position: static; color: var(--paper); font-size: 17px; letter-spacing: 2.5px; gap: 14px; }
  .brand--back .brand__mark { background: var(--paper); width: 18px; height: 18px; }
  .back__services {
    position: absolute; left: 0; right: 0; bottom: 0; height: 65px;
    background: var(--charcoal);
    border-top: 2px solid var(--paper);
    display: flex; flex-direction: column; justify-content: center; align-items: center;
    font-family: "Raleway", sans-serif; font-weight: 600;
    font-size: 10.6px; color: var(--paper); line-height: 14px;
  }
</style>
</head>
<body>
  <section class="card card--front">
    <div class="front__stripe"></div>
    <div class="brand brand--front">
      <span class="brand__mark"></span>
      <span class="brand__name">Harbourline<br>Electrical<br>Solutions</span>
    </div>
    <p class="front__sectors">COMMERCIAL INDUSTRIAL RESIDENTIAL</p>
    <div class="person">
      <p class="person__name">MARCUS T. HOLLINGS</p>
      <p class="person__role">Project Manager</p>
    </div>
    <div class="contact">
      <p class="contact__row">
        <svg class="contact__icon" viewBox="0 0 10 12" aria-hidden="true"><rect x="1.5" y="0.7" width="7" height="10.6" rx="1.2" fill="none" stroke="#3a3a3a" stroke-width="1.3"/><rect x="4" y="9" width="2" height="1" fill="#3a3a3a"/></svg>
        (441) 555-0187
      </p>
      <p class="contact__row">
        <svg class="contact__icon" viewBox="0 0 10 10" aria-hidden="true"><rect x="0" y="1.5" width="10" height="7" fill="var(--teal)"/><path d="M0 1.8 L5 5.6 L10 1.8" fill="none" stroke="#fff" stroke-width="1"/></svg>
        hlelectricalsolutions@mailvento.com
      </p>
    </div>
    <div class="social">
      <span class="social__dot"></span>
      @hlelectricalsolutions
    </div>
  </section>

  <section class="card card--back">
    <div class="back__brand-area">
      <div class="brand brand--back">
        <span class="brand__mark"></span>
        <span class="brand__name">Harbourline<br>Electrical<br>Solutions</span>
      </div>
    </div>
    <div class="back__services">
      <p>ELECTRICAL CONSTRUCTION &amp; MAINTENANCE</p>
      <p>LED LIGHTING &amp; AUTOMATION | DATA &amp; COMMUNICATION</p>
      <p>LIFE SAFETY SYSTEMS (FIRE ALARM / SECURITY)</p>
    </div>
  </section>
</body>
</html>
```